ORV Fashion Design Company Needs a New Web Design, Please Click Me

Designers:

PLEASE NOTE: we only need the web page design, not a fully coded website.

Our brand's name is Orbel Vantra, our signature is print. our style is edgy and chic.

The old website is too messy. here's the address:
www.orvdesign.example.cn

The new website's purpose is to show our brand/design and most importantly, sell products, So it should be a combination of a designer official website and online shopping. I want the whole style to be clean, edgy and pioneer, easy to understand. we need a sophisticated online shopping website.

The reference websites are:
liromapek.example.uk
www.qd-besu.example
talemkorv.example
misolvare.example
pardelunitram.example

Please beat their designs :)

Check out our lasted fashion show to get to know us more.

https://www.videohost.example/watch?v=ZkrpLmWnaYd&spfreload=10

The attachments are our Logo and some 2015 Look Book.
(Please let us know if you want to play with our print in this particular web design, we can send the source file.)
Updates

Designers, we really like the design of helenamardoux.example(we have attached a picture of the website) , Can we get a homepage like that? so the designs you submit will be 3 pages. The first one should be a page that only has Shop/Look. then the shop page, it should be nothing but our product which we will list the categories ourself. And the look page should contain all the info. such as news, about us and designers etc. Thank you all for your hard work, we really enjoyed the designs. Added Monday, November 03, 2014

Target Market(s)

Our target audiences are woman aged from 16-40 who like online shopping

Industry/Entity Type

Online Shopping

Number of Pages Required

3 page

Font styles to use
Serif
Sans Serif
Script

Requirements
Must have
• Designers,
• we really like the design of helenamardoux.example(we have attached a picture of the website) , Can we get a homepage like that? so the designs you submit will be 3 pages. The first one should be a page that only has Shop/Look. then the shop page, it should be nothing but our product which we will list the categories ourself. And the look page should contain all the info. such as news, about us and designers etc. Thank you all for your hard work, we really enjoyed the designs.

```html
<!DOCTYPE html>
<html lang="en">
<head>
<meta charset="utf-8">
<title>ORV Group – Latest News</title>
<link href="https://fonts.googleapis.com/css2?family=Didact+Gothic&family=EB+Garamond:wght@400&display=swap" rel="stylesheet">
<style>
  :root {
    --side-bg: #ebe9e6;
    --panel-bg: #f6f6f6;
    --brand-red: #b8141c;
    --text-dark: #4a4a4a;
    --text-body: #555555;
    --text-light: #b5b5b5;
    --icon-grey: #c4c4c4;
  }
  * { margin: 0; padding: 0; box-sizing: border-box; }
  html, body { width: 1200px; height: 781px; overflow: hidden; }
  body {
    position: relative;
    background: var(--side-bg);
    font-family: "Didact Gothic", "Helvetica Neue", Arial, sans-serif;
    color: var(--text-body);
  }
  .sidebar { position: absolute; left: 0; top: 0; width: 280px; height: 781px; }
  .brand { position: absolute; left: 40px; top: 96px; width: 204px; text-align: center; }
  .brand-mark { display: block; width: 66px; height: 66px; margin: 0 auto 4px; border-radius: 50%; background: var(--brand-red); }
  .brand-name {
    font-family: "EB Garamond", Georgia, serif;
    font-size: 16px; line-height: 16px; letter-spacing: 1.3px;
    color: var(--text-dark); text-transform: uppercase;
  }
  .main-nav { position: absolute; right: 51px; top: 463px; text-align: right; }
  .main-nav a {
    display: block; position: relative;
    font-size: 12px; line-height: 15.6px; letter-spacing: 4.6px;
    color: var(--text-dark); text-decoration: none; text-transform: uppercase;
    margin-right: -4.6px;
  }
  .main-nav a.is-active::after {
    content: ""; position: absolute; right: -10px; top: 4px;
    border-left: 5px solid var(--brand-red);
    border-top: 4px solid transparent; border-bottom: 4px solid transparent;
  }
  .social { position: absolute; left: 135px; top: 620px; display: flex; gap: 2px; }
  .social span { width: 21px; height: 21px; background: var(--icon-grey); }
  .hero {
    position: absolute; left: 280px; top: 0; width: 642px; height: 198px;
    background:
      radial-gradient(ellipse at 70% 30%, rgba(110,170,190,.55), transparent 55%),
      radial-gradient(ellipse at 35% 75%, rgba(200,110,90,.45), transparent 45%),
      linear-gradient(100deg, #2a2420 0%, #3c3a40 40%, #2d3640 65%, #4a2e28 100%);
  }
  .hero::before { content: ""; position: absolute; left: 0; top: 0; width: 13px; height: 100%; background: var(--brand-red); }
  .content { position: absolute; left: 280px; top: 198px; width: 642px; height: 583px; background: var(--panel-bg); }
  .section-title { position: absolute; left: 30px; top: 31px; font-weight: 400; }
  .section-title .kicker { display: block; font-size: 18px; line-height: 17px; color: var(--text-light); }
  .section-title .headline { display: block; font-size: 20px; line-height: 19px; color: var(--text-dark); }
  .news-column { position: absolute; top: 70px; width: 280px; font-size: 10.2px; line-height: 18px; color: var(--text-body); }
  .news-column p + p { margin-top: 18px; }
  .news-column.first { left: 33px; }
  .news-column.second { left: 332px; }
</style>
</head>
<body>
  <aside class="sidebar">
    <div class="brand">
      <span class="brand-mark"></span>
      <div class="brand-name">ORV Group<br>Orbel Vantra</div>
    </div>
    <nav class="main-nav">
      <a href="#">Home</a>
      <a href="#">About</a>
      <a href="#">Videos</a>
      <a href="#" class="is-active">News</a>
      <a href="#">Collection</a>
      <a href="#">Shop</a>
      <a href="#">Contact</a>
    </nav>
    <div class="social" aria-label="Social links">
      <span role="img" aria-label="Social link 1"></span>
      <span role="img" aria-label="Social link 2"></span>
      <span role="img" aria-label="Social link 3"></span>
      <span role="img" aria-label="Social link 4"></span>
    </div>
  </aside>

  <div class="hero" role="img" aria-label="Boutique interior with a coral dress on a mannequin, colourful garments on rails and a lit dotted ceiling"></div>

  <main class="content">
    <h1 class="section-title"><span class="kicker">ORV</span><span class="headline">LATEST NEWS</span></h1>
    <div class="news-column first">
      <p>At vero eos et accusamus et iusto odio dignissimos ducimus qui blanditiis praesentium voluptatum deleniti atque corrupti quos dolores et quas molestias excepturi sint occaecati cupiditate non provident, similique sunt in culpa qui officia deserunt mollitia animi, id est laborum et dolorum fuga.</p>
      <p>Et harum quidem rerum facilis est et expedita distinctio. Nam libero tempore, cum soluta nobis est eligendi optio cumque nihil impedit quo minus id quod maxime placeat facere possimus, omnis voluptas assumenda est, omnis dolor repellendus. Temporibus autem quibusdam et aut officiis debitis aut rerum necessitatibus saepe eveniet ut et voluptates repudiandae sint et molestiae non recusandae. Itaque earum rerum hic tenetur a sapiente delectus, ut aut reiciendis voluptatibus maiores alias consequatur aut perferendis doloribus asperiores repellat.</p>
      <p>At vero eos et accusamus et iusto odio dignissimos ducimus qui blanditiis praesentium voluptatum deleniti atque corrupti quos dolores et quas molestias excepturi sint occaecati cupiditate non provident, similique sunt in culpa qui officia deserunt mollitia animi,</p>
    </div>
    <div class="news-column second">
      <p>id est laborum et dolorum fuga.</p>
      <p>Et harum quidem rerum facilis est et expedita distinctio. Nam libero tempore, cum soluta nobis est eligendi optio cumque nihil impedit quo minus id quod maxime placeat facere possimus, omnis voluptas assumenda est, omnis dolor repellendus. Temporibus autem quibusdam et aut officiis debitis aut rerum necessitatibus saepe eveniet ut et voluptates repudiandae sint et molestiae non recusandae. Itaque earum rerum hic tenetur a sapiente delectus, ut aut reiciendis voluptatibus maiores alias consequatur aut perferendis doloribus asperiores repellat.</p>
    </div>
  </main>
</body>
</html>
```